Elevating our current Business Card Design

We want to elevate our current business card with a new design to look like a zenith 300 company. We are a premium lubricant distributor (oil and grease).
We need 2 versions, version 1 is as per the uploaded a copy of our current business card with the English version.
For our Chinese version we need to use the front to be English in English and have the back of the card designed exactly like the front for all info to be in Chinese.
The design template needs to be such that we can amend the template with adding different information for each person's card.
The background colour of the card can be changed- we just need to clearly see all information on the card and logos.
The QJR and Ember steady logos cannot have any colour or display changes- only use the logos attached.
All logos need to be included and all information from the attached current card

```html
<!DOCTYPE html>
<html lang="en">
<head>
<meta charset="utf-8">
<title>Meridian Business Card</title>
<link href="https://fonts.googleapis.com/css2?family=Open+Sans:wght@400;600;700&display=swap" rel="stylesheet">
<style>
  :root {
    --stage: #232323;
    --card-green: #06301f;
    --brand-red: #e8302a;
    --brand-gold: #e6ad2c;
    --paper: #ffffff;
    --ink-light: #ffffff;
    --ink-dark: #0c3a26;
    --badge-fill: #e4e6e5;
  }
  * { box-sizing: border-box; margin: 0; padding: 0; }
  html, body { width: 1200px; height: 780px; overflow: hidden; }
  body {
    background: var(--stage);
    font-family: "Open Sans", Arial, sans-serif;
    position: relative;
  }
  .card {
    position: absolute;
    width: 555px;
    height: 317px;
    background: var(--card-green);
    border-radius: 3px;
    box-shadow: 0 10px 24px rgba(0,0,0,.55);
    overflow: hidden;
  }
  .card--front { left: 30px; top: 231px; }
  .card--back { left: 615px; top: 231px; }

  /* Front */
  .front-mark {
    position: absolute;
    left: 50%; top: 50%;
    transform: translate(-50%, -50%);
    display: flex; align-items: center; gap: 18px;
  }
  .front-mark__dot {
    width: 34px; height: 34px; border-radius: 50%;
    background: var(--brand-gold);
  }
  .front-mark__name {
    font-weight: 700; font-size: 58px; letter-spacing: 2px;
    color: var(--brand-red);
  }

  /* Back: partner strip */
  .partner-strip {
    position: absolute; left: 0; top: 0; bottom: 0;
    width: 150px;
    background: var(--paper);
    padding: 16px 12px;
    display: flex; flex-direction: column; justify-content: space-between;
  }
  .partner-strip__member {
    display: flex; align-items: center; gap: 6px;
    color: var(--ink-dark);
  }
  .partner-strip__member-name { font-weight: 700; font-size: 12px; line-height: 1.1; }
  .partner-strip__member-note { font-size: 6px; letter-spacing: .6px; text-transform: uppercase; }
  .partner-strip__ring {
    width: 16px; height: 16px; border-radius: 50%;
    border: 3px solid var(--ink-dark);
  }
  .partner-strip__company {
    border: 1.5px solid var(--brand-red);
    border-radius: 6px;
    padding: 8px;
    color: var(--brand-red);
  }
  .partner-strip__company-name { font-weight: 700; font-size: 15px; }
  .partner-strip__company-note { font-size: 7px; text-transform: uppercase; line-height: 1.3; margin-top: 3px; }
  .partner-strip__supplier { color: var(--brand-red); }
  .partner-strip__supplier-name { font-weight: 700; font-size: 16px; letter-spacing: .5px; }
  .partner-strip__supplier-note { font-size: 7px; text-transform: uppercase; letter-spacing: .8px; }
  .cert-row { display: flex; justify-content: space-between; }
  .cert-badge {
    width: 32px; height: 32px; border-radius: 4px;
    background: var(--badge-fill);
  }

  /* Back: contact block */
  .name-bar {
    position: absolute; right: 0; top: 34px;
    width: 12px; height: 34px;
    background: var(--brand-red);
  }
  .contact {
    position: absolute; right: 30px; top: 30px;
    text-align: right;
    color: var(--ink-light);
  }
  .contact__name {
    font-weight: 700; font-size: 26px; line-height: 1.05;
    color: var(--brand-red);
  }
  .contact__role { font-weight: 600; font-size: 12px; margin-bottom: 10px; }
  .contact__address { font-size: 12px; line-height: 1.35; margin-bottom: 10px; }
  .contact__list { list-style: none; font-size: 12px; line-height: 1.6; }
  .contact__list li { display: flex; justify-content: flex-end; align-items: center; gap: 8px; }
  .contact__icon { width: 12px; height: 12px; flex: none; }
  .contact__icon * { stroke: var(--brand-red); fill: none; stroke-width: 1.6; }
</style>
</head>
<body>

<section class="card card--front" aria-label="Card front">
  <div class="front-mark">
    <span class="front-mark__dot"></span>
    <span class="front-mark__name">MERIDIAN</span>
  </div>
</section>

<section class="card card--back" aria-label="Card back">
  <aside class="partner-strip">
    <div class="partner-strip__member">
      <span class="partner-strip__ring"></span>
      <div>
        <div class="partner-strip__member-name">Ember steady</div>
        <div class="partner-strip__member-note">Network member</div>
      </div>
    </div>
    <div class="partner-strip__company">
      <div class="partner-strip__company-name">Meridian</div>
      <div class="partner-strip__company-note">Meridian Oil<br>Distributors</div>
    </div>
    <div class="partner-strip__supplier">
      <div class="partner-strip__supplier-name">HALVARD</div>
      <div class="partner-strip__supplier-note">Premium lubricants</div>
    </div>
    <div class="cert-row" aria-label="QJR certifications">
      <span class="cert-badge"></span>
      <span class="cert-badge"></span>
      <span class="cert-badge"></span>
    </div>
  </aside>

  <span class="name-bar"></span>
  <div class="contact">
    <h1 class="contact__name">Mara Lindqvist</h1>
    <p class="contact__role">Administration Executive</p>
    <p class="contact__address">48 Harbour Freight Way<br>Bexley, WA 6190</p>
    <ul class="contact__list">
      <li>1300 604 417
        <svg class="contact__icon" viewBox="0 0 12 12"><path d="M2 1.5 4 1l1 2.5-1.2.8a6 6 0 0 0 3.9 3.9l.8-1.2L11 8l-.5 2C6 10.5 1.5 6 2 1.5z"/></svg></li>
      <li>+61 400 218 736
        <svg class="contact__icon" viewBox="0 0 12 12"><rect x="3" y="1" width="6" height="10" rx="1"/></svg></li>
      <li>+61 8 9000 5120
        <svg class="contact__icon" viewBox="0 0 12 12"><rect x="1.5" y="4.5" width="9" height="6" rx="1"/><rect x="3.5" y="1.5" width="5" height="3"/></svg></li>
      <li>www.meridianoildist.com
        <svg class="contact__icon" viewBox="0 0 12 12"><circle cx="6" cy="6" r="4.8"/><path d="M1.2 6h9.6M6 1.2c2.5 2.6 2.5 7 0 9.6M6 1.2c-2.5 2.6-2.5 7 0 9.6"/></svg></li>
      <li>mara.l@meridianoildist.com
        <svg class="contact__icon" viewBox="0 0 12 12"><rect x="1" y="2.5" width="10" height="7" rx="1"/><path d="m1 3 5 4 5-4"/></svg></li>
    </ul>
  </div>
</section>

</body>
</html>
```